Real Estate Media Company Business Card

’m looking for a modern, high-end, double-sided business card for:
Bright Harbor Studios LLC
(Real Estate Photography & Videography)
The design should feel clean, minimal, and premium, appealing to top real estate agents and brokers.
👉 Horizontal layout is preferred
👉 Vertical option is welcome but not required
⸻
Front Side (Main Information):
Include:
* Desmond Whitfield
* Bright Harbor Studios LLC
* Title (open to creative improvement)
* Phone Number
* Email
* Website
⸻
Services Section (VERY IMPORTANT):
This should be a key visual element, not an afterthought.
Services to Include:
* Cinematic Video
* Real Estate Photography
* Drone
* Social Media Reels
* Floor Plans
* Use clean, modern icons next to each service
* Icons should be simple, minimal, and consistent style (outline or thin line preferred)
* Option to place icons inside small circles (like reference)
Layout:
* Format services similar to a clean horizontal or grid-style list (like “example 2”)
* Keep spacing balanced and uncluttered
* Make this section visually appealing and easy to scan
⸻
Back Side:
* Keep it extremely minimal
* Only include the logo in a corner
* No additional text needed
⸻
Typography & Style:
* Modern, clean, slightly bold fonts (based on uploaded references)
* Strong hierarchy (name + services stand out most)
* Plenty of white/negative space
* Avoid clutter
⸻
Overall Feel:
* Luxury
* Modern
* Clean
* Confident
* High-end real estate branding
⸻
Notes for Designers:
* Simplicity is key
* Services section should feel polished and intentional
* This card should feel like something a top-producing real estate agent would keep
Target Market(s)
Real estate agent agents

```html
<!DOCTYPE html>
<html lang="en">
<head>
<meta charset="utf-8">
<title>Bright Harbor Studios – Business Card</title>
<link href="https://fonts.googleapis.com/css2?family=Ubuntu:wght@400;500;700&display=swap" rel="stylesheet">
<style>
  :root {
    --navy: #0f1f33;
    --slate: #95a0a9;
    --muted: #8793a0;
    --white: #ffffff;
    --icon: #c9d0d7;
    --rule: #6c7885;
    --backdrop: #4a3f33;
  }
  * { margin: 0; padding: 0; box-sizing: border-box; }
  html, body {
    width: 1060px; height: 1200px; overflow: hidden;
    background: var(--backdrop);
    font-family: "Ubuntu", sans-serif;
  }
  .card {
    position: absolute; left: 84px; width: 892px; height: 510px;
    border-radius: 26px; overflow: hidden;
    box-shadow: 0 10px 28px rgba(0,0,0,0.35);
  }
  .card--front { top: 40px; background: var(--navy); color: var(--white); }
  .card--back { top: 650px; background: var(--slate); }

  .identity { position: absolute; left: 45px; top: 36px; }
  .identity__name { font-size: 51px; font-weight: 500; line-height: 1.1; letter-spacing: 0.3px; }
  .identity__title { font-size: 31px; color: var(--muted); line-height: 1.2; margin-top: 0; }
  .identity__company { font-size: 34px; font-weight: 500; line-height: 1.3; margin-top: 4px; }

  .services-rule {
    position: absolute; left: 429px; top: 190px; width: 3px; height: 190px;
    background: var(--rule);
  }
  .services { position: absolute; left: 460px; top: 179px; list-style: none; }
  .services__item {
    display: flex; align-items: center; height: 42.5px;
    font-size: 29px; letter-spacing: 0.3px;
  }
  .services__icon { width: 40px; height: 26px; margin-right: 17px; flex: none; }

  .contact { position: absolute; left: 45px; top: 370px; list-style: none; }
  .contact__item {
    display: flex; align-items: center; height: 38.5px;
    font-size: 26px; letter-spacing: 0.2px;
  }
  .contact__icon { width: 28px; height: 28px; margin-right: 15px; flex: none; }

  .back-band {
    position: absolute; left: 0; bottom: 0; width: 100%; height: 178px;
    background: var(--navy);
  }
  .brand-mark {
    position: absolute; left: 724px; top: 345px; transform: translateX(-50%);
    display: flex; flex-direction: column; align-items: center;
    color: var(--white);
  }
  .brand-mark__dot {
    width: 46px; height: 46px; border-radius: 50%;
    border: 3px solid var(--white); margin-bottom: 14px;
  }
  .brand-mark__name {
    font-size: 21px; font-weight: 400; letter-spacing: 2.5px; white-space: nowrap;
  }
</style>
</head>
<body>

<svg width="0" height="0" style="position:absolute">
  <defs>
    <symbol id="icon-camera" viewBox="0 0 40 26">
      <g fill="none" stroke="currentColor" stroke-width="1.2">
        <rect x="1" y="5" width="38" height="20" rx="2"/>
        <path d="M13 5 L15 1 H25 L27 5"/>
        <circle cx="20" cy="15" r="7"/>
        <circle cx="20" cy="15" r="4.5"/>
        <rect x="32" y="8" width="4" height="2.5"/>
      </g>
    </symbol>
  </defs>
</svg>

<section class="card card--front">
  <div class="identity">
    <h1 class="identity__name">Desmond Whitfield</h1>
    <p class="identity__title">Founder | Real Estate Media Specialist</p>
    <p class="identity__company">Bright Harbor Studios LLC</p>
  </div>

  <div class="services-rule"></div>
  <ul class="services">
    <li class="services__item"><svg class="services__icon" style="color:var(--icon)"><use href="#icon-camera"/></svg>Cinematic Video</li>
    <li class="services__item"><svg class="services__icon" style="color:var(--icon)"><use href="#icon-camera"/></svg>Real Estate Photography</li>
    <li class="services__item"><svg class="services__icon" style="color:var(--icon)"><use href="#icon-camera"/></svg>Drone</li>
    <li class="services__item"><svg class="services__icon" style="color:var(--icon)"><use href="#icon-camera"/></svg>Social Media Reels</li>
    <li class="services__item"><svg class="services__icon" style="color:var(--icon)"><use href="#icon-camera"/></svg>Floor Plans</li>
  </ul>

  <ul class="contact">
    <li class="contact__item">
      <svg class="contact__icon" viewBox="0 0 24 24"><path fill="#b7c0c9" d="M6.6 10.8a15.1 15.1 0 0 0 6.6 6.6l2.2-2.2a1 1 0 0 1 1-.25 11.4 11.4 0 0 0 3.6.57 1 1 0 0 1 1 1V20a1 1 0 0 1-1 1A17 17 0 0 1 3 4a1 1 0 0 1 1-1h3.5a1 1 0 0 1 1 1c0 1.25.2 2.45.57 3.57a1 1 0 0 1-.25 1z"/></svg>
      555-014-2298
    </li>
    <li class="contact__item">
      <svg class="contact__icon" viewBox="0 0 24 24"><rect x="2" y="5" width="20" height="14" fill="#b7c0c9"/><path d="M2 5 L12 13 L22 5" fill="none" stroke="var(--navy)" stroke-width="1.6"/></svg>
      desmond@brightharborstudios.com
    </li>
    <li class="contact__item">
      <svg class="contact__icon" viewBox="0 0 24 24"><g fill="none" stroke="#b7c0c9" stroke-width="1.5"><circle cx="12" cy="12" r="10"/><ellipse cx="12" cy="12" rx="4.5" ry="10"/><path d="M2 12h20M4 7h16M4 17h16M12 2v20"/></g></svg>
      www.brightharborstudios.com
    </li>
  </ul>
</section>

<section class="card card--back">
  <div class="back-band"></div>
  <div class="brand-mark">
    <span class="brand-mark__dot"></span>
    <span class="brand-mark__name">BRIGHT HARBOR STUDIOS</span>
  </div>
</section>

</body>
</html>
```